New Business Card Design Project

Use the flyer uploaded and website www.brightoakbuilders.com for inspiration.
List Our Services on Backside of business cards
Marcus Delling
Harborline Builders Inc.
Licensed General Contractors
858-471-6093

Contact Information for Business Card

Use the flyer uploaded and website www.brightoakbuilders.com for inspiration. List Our Services on Backside of business cards Marcus Delling Harborline Builders Inc. Licensed General Contractors 858-471-6093

```html
<!DOCTYPE html>
<html lang="en">
<head>
<meta charset="utf-8">
<title>Harborline Builders – Business Card</title>
<link href="https://fonts.googleapis.com/css2?family=Open+Sans:wght@400;600;700&family=Roboto:wght@400;700&display=swap" rel="stylesheet">
<style>
  :root {
    --bg: #232323;
    --card-white: #ffffff;
    --card-black: #1b1b1b;
    --brand-red: #ed1c24;
    --brand-blue: #2e3192;
    --accent-blue: #4a7bd0;
    --ink: #1a1a1a;
    --paper-text: #f2f2f2;
  }
  * { margin: 0; padding: 0; box-sizing: border-box; }
  html, body { width: 1200px; height: 780px; overflow: hidden; background: var(--bg); }
  .canvas { position: relative; width: 1200px; height: 780px; }

  .card {
    position: absolute; top: 235px; width: 540px; height: 310px;
    overflow: hidden; font-family: "Open Sans", sans-serif;
    box-shadow: 0 14px 30px rgba(0,0,0,.45);
  }
  .card--front { left: 40px; background: var(--card-white); color: var(--ink); }
  .card--back { left: 620px; background: var(--card-black); color: var(--paper-text); }

  .front-sweep { position: absolute; inset: 0; width: 100%; height: 100%; }

  .wordmark {
    font-family: "Open Sans", sans-serif; font-weight: 400;
    text-transform: uppercase; white-space: nowrap;
  }
  .card--front .wordmark {
    position: absolute; left: 236px; top: 48px;
    font-size: 18px; letter-spacing: 2px; color: var(--ink);
  }

  .person { position: absolute; left: 56px; top: 86px; }
  .person__name { font-family: "Roboto", sans-serif; font-weight: 700; font-size: 28px; color: var(--brand-red); line-height: 1.1; }
  .person__title { font-size: 12px; color: var(--ink); margin-top: 4px; }

  .divider { position: absolute; left: 238px; top: 146px; width: 1.5px; height: 76px; background: var(--brand-red); }

  .contacts { position: absolute; left: 256px; top: 148px; list-style: none; }
  .contacts li { display: flex; align-items: center; gap: 8px; font-size: 14px; line-height: 24px; color: var(--ink); }
  .contacts svg { width: 14px; height: 14px; flex: none; }

  .company-line { position: absolute; left: 42px; bottom: 22px; font-family: "Roboto", sans-serif; font-size: 15px; color: var(--card-white); }

  .card--back .wordmark { position: absolute; left: 0; right: 0; top: 52px; text-align: center; font-size: 26px; letter-spacing: 3px; color: var(--paper-text); }

  .headline { position: absolute; left: 0; right: 0; top: 118px; text-align: center; font-family: "Roboto", sans-serif; font-weight: 700; }
  .headline__guarantee { font-size: 14px; color: var(--brand-red); letter-spacing: .3px; }
  .headline__special { font-size: 13px; color: var(--accent-blue); margin-top: 2px; }
  .rule { position: absolute; top: 138px; height: 1.5px; width: 120px; background: var(--accent-blue); }
  .rule--left { left: 22px; }
  .rule--right { right: 22px; }

  .services { position: absolute; left: 14px; right: 14px; top: 186px; list-style: none; text-align: center; }
  .services li { font-size: 10.6px; line-height: 26px; white-space: nowrap; }
  .services span { display: inline-flex; align-items: center; gap: 3px; margin: 0 3px; }
  .services svg { width: 9px; height: 9px; }
</style>
</head>
<body>
<main class="canvas">

  <section class="card card--front" aria-label="Business card front">
    <svg class="front-sweep" viewBox="0 0 540 310" preserveAspectRatio="none" aria-hidden="true">
      <path d="M0 96 C70 215 270 300 540 286 L540 310 L0 310 Z" fill="var(--brand-red)"/>
      <path d="M22 80 C85 200 275 288 540 274" fill="none" stroke="var(--card-white)" stroke-width="7"/>
      <path d="M20 78 C83 198 273 286 520 274" fill="none" stroke="var(--brand-blue)" stroke-width="2.2"/>
    </svg>

    <div class="wordmark">Harborline Builders</div>

    <div class="person">
      <div class="person__name">Marcus Delling</div>
      <div class="person__title">Licensed General Contractors</div>
    </div>

    <div class="divider"></div>

    <ul class="contacts">
      <li>
        <svg viewBox="0 0 16 16" aria-hidden="true"><path d="M4 1.5l2.5 3-1.6 1.6a9 9 0 0 0 5 5L11.5 9.5l3 2.5-1.5 2.5C7 14.5 1.5 9 1.5 3z" fill="var(--brand-red)"/></svg>
        858-471-6093
      </li>
      <li>
        <svg viewBox="0 0 16 16" aria-hidden="true"><rect x="1" y="3" width="14" height="10" rx="1" fill="var(--brand-red)"/><path d="M1.5 3.5L8 9l6.5-5.5" fill="none" stroke="#fff" stroke-width="1.3"/></svg>
        info@brightoakbuilders.com
      </li>
      <li>
        <svg viewBox="0 0 16 16" aria-hidden="true"><circle cx="8" cy="8" r="7" fill="var(--brand-red)"/><path d="M1 8h14M8 1c-3 3-3 11 0 14M8 1c3 3 3 11 0 14" fill="none" stroke="#fff" stroke-width="1"/></svg>
        www.brightoakbuilders.com
      </li>
    </ul>

    <div class="company-line">Harborline Builders Inc.</div>
  </section>

  <section class="card card--back" aria-label="Business card back">
    <div class="wordmark">Harborline Builders</div>

    <span class="rule rule--left"></span>
    <span class="rule rule--right"></span>
    <div class="headline">
      <div class="headline__guarantee">OUR SERVICES ARE 100% GUARANTEED</div>
      <div class="headline__special">SPECIALIZING IN:</div>
    </div>

    <ul class="services">
      <li>
        <span><svg viewBox="0 0 10 10" aria-hidden="true"><circle cx="5" cy="5" r="4.3" fill="none" stroke="var(--brand-red)"/><path d="M2.8 5.2l1.6 1.5 3-3.2" fill="none" stroke="var(--brand-red)" stroke-width="1.2"/></svg>Remodel: Kitchen &amp; Bath</span>
        <span><svg viewBox="0 0 10 10" aria-hidden="true"><circle cx="5" cy="5" r="4.3" fill="none" stroke="var(--brand-red)"/><path d="M2.8 5.2l1.6 1.5 3-3.2" fill="none" stroke="var(--brand-red)" stroke-width="1.2"/></svg>Painting: Interior &amp; Exterior</span>
        <span><svg viewBox="0 0 10 10" aria-hidden="true"><circle cx="5" cy="5" r="4.3" fill="none" stroke="var(--brand-red)"/><path d="M2.8 5.2l1.6 1.5 3-3.2" fill="none" stroke="var(--brand-red)" stroke-width="1.2"/></svg>Flooring: Carpet, Vinyl, Wood</span>
      </li>
      <li>
        <span><svg viewBox="0 0 10 10" aria-hidden="true"><circle cx="5" cy="5" r="4.3" fill="none" stroke="var(--brand-red)"/><path d="M2.8 5.2l1.6 1.5 3-3.2" fill="none" stroke="var(--brand-red)" stroke-width="1.2"/></svg>Window &amp; Door Replacement</span>
        <span><svg viewBox="0 0 10 10" aria-hidden="true"><circle cx="5" cy="5" r="4.3" fill="none" stroke="var(--brand-red)"/><path d="M2.8 5.2l1.6 1.5 3-3.2" fill="none" stroke="var(--brand-red)" stroke-width="1.2"/></svg>Plumbing: Repairs &amp; Upgrades</span>
        <span><svg viewBox="0 0 10 10" aria-hidden="true"><circle cx="5" cy="5" r="4.3" fill="none" stroke="var(--brand-red)"/><path d="M2.8 5.2l1.6 1.5 3-3.2" fill="none" stroke="var(--brand-red)" stroke-width="1.2"/></svg>Energy-Efficient Upgrades</span>
      </li>
      <li>
        <span><svg viewBox="0 0 10 10" aria-hidden="true"><circle cx="5" cy="5" r="4.3" fill="none" stroke="var(--brand-red)"/><path d="M2.8 5.2l1.6 1.5 3-3.2" fill="none" stroke="var(--brand-red)" stroke-width="1.2"/></svg>Deck &amp; Patio Construction</span>
        <span><svg viewBox="0 0 10 10" aria-hidden="true"><circle cx="5" cy="5" r="4.3" fill="none" stroke="var(--brand-red)"/><path d="M2.8 5.2l1.6 1.5 3-3.2" fill="none" stroke="var(--brand-red)" stroke-width="1.2"/></svg>Water &amp; Mold Damage</span>
        <span><svg viewBox="0 0 10 10" aria-hidden="true"><circle cx="5" cy="5" r="4.3" fill="none" stroke="var(--brand-red)"/><path d="M2.8 5.2l1.6 1.5 3-3.2" fill="none" stroke="var(--brand-red)" stroke-width="1.2"/></svg>Garage Renovation</span>
      </li>
    </ul>
  </section>

</main>
</body>
</html>
```